military training website velmotrail.com

I have a website that someone designed I am not happy with. It looks like the designer did not have the artistic ability to make a quality product. the power points are ideas that I had for the website. the business proposal was designed by someone else, and I like the style and font used, the website should reflect this document. The main part of the website should be informational with few pictures, maybe some background images behind or off to the side of the text. I would like to include a generic map with four locations marked, which, when you hover the cursor over them, show a picture of the actual location with an artistic effect or blurred so it doesn't look like a plivora atlas snip, and a picture that resembles what services are offered there, along with the text description, pictures can be found in the documents I attached, also can be stock images. this is outlined in the power points roughly.
Want to have the side menu of the major topics, or at the top, and scroll down a single page to find all of the information we have to offer

Target Market(s)

Special operations military

Industry/Entity Type

military

Coding

Coded - Design and coding required

Number of Pages Required

1 page

Other font styles liked:
• Agency FB

Colors
0054AA
0677BA
7BADD7
CADEEF
E8F1F8
00AB8E
00BBA5
67D7C9
C6EFE9
E9F9F6

Requirements
Must have
• interactive "map"
Nice to have
• professional design features to make it look like a professional website, not a beginner designer

```html
<!DOCTYPE html>
<html lang="en">
<head>
<meta charset="utf-8">
<title>Velmo Trail — Master The Mission</title>
<link href="https://fonts.googleapis.com/css2?family=Orbitron:wght@500;600;700&family=Michroma&family=Arimo:wght@400;700&display=swap" rel="stylesheet">
<style>
:root{
  --navy:#121d3b;
  --navy-deep:#0c1530;
  --steel:#4f81b6;
  --steel-light:#6d9acb;
  --marker:#3b5bf5;
  --ink:#1b1b1b;
  --body:#2a2a2a;
  --mist:#f3f4f7;
  --white:#ffffff;
  --black:#000000;
}
*{margin:0;padding:0;box-sizing:border-box}
html,body{width:1200px;height:4870px;overflow:hidden}
body{position:relative;background:var(--white);font-family:"Arimo",Arial,sans-serif;color:var(--body)}
.display{font-family:"Orbitron",sans-serif;font-weight:600}
.nav-font{font-family:"Michroma",sans-serif}

/* header */
.site-header{position:absolute;top:0;left:0;width:1200px;height:85px;background:var(--white);z-index:5}
.site-header a{position:absolute;top:33px;font-family:"Michroma",sans-serif;font-size:14px;color:var(--ink);text-decoration:none}
.brand-badge{position:absolute;left:540px;top:8px;width:120px;height:120px;border-radius:50%;background:var(--navy);border:4px solid var(--white);box-shadow:0 2px 8px rgba(0,0,0,.25);display:flex;align-items:center;justify-content:center;z-index:6}
.brand-badge span{font-family:"Michroma",sans-serif;font-size:12px;color:var(--white);text-align:center;line-height:1.5}

/* hero */
.hero{position:absolute;top:85px;left:0;width:1200px;height:601px;background:linear-gradient(180deg,#6f7a5c 0%,#5f7c43 35%,#4f7a2e 70%,#4a6f2a 100%)}
.hero-panel{position:absolute;left:300px;top:183px;width:600px;height:237px;background:rgba(40,40,40,.55);border-radius:12px;text-align:center;color:var(--white)}
.hero-panel h1{font-family:"Orbitron",sans-serif;font-weight:700;font-size:54px;letter-spacing:2px;margin-top:68px}
.hero-panel p{font-family:"Michroma",sans-serif;font-size:20px;margin-top:14px}

/* provide */
.provide{position:absolute;top:686px;left:0;width:1200px;height:1191px;background:linear-gradient(135deg,#eceef2 0%,#f8f9fb 45%,#eef0f4 100%)}
.section-title{font-family:"Orbitron",sans-serif;font-weight:600;font-size:32px;color:var(--black);text-align:center}
.provide .section-title{position:absolute;top:88px;width:1200px}
.lead{position:absolute;left:119px;width:962px;top:152px;text-align:center;font-size:13.5px;line-height:31px;color:var(--body)}
.feature h3{font-family:"Michroma",sans-serif;font-weight:400;font-size:16.5px;color:var(--black);margin-bottom:8px}
.feature p{font-size:12.2px;line-height:27.5px;color:var(--body)}
.feature{position:absolute;width:420px}
.feature.left{text-align:right}
.feature.top{left:300px;width:600px;top:311px;text-align:center}
.feature.top p{line-height:27px}
.spine{position:absolute;left:0;top:0}
.hex{position:absolute;width:84px;height:84px}

.closing{position:absolute;top:1843px;left:150px;width:900px;text-align:center;font-size:13.5px;line-height:27.5px;color:var(--body)}

/* mission block */
.mission-block{position:absolute;top:2049px;left:98px;width:1002px;height:317px;display:flex}
.mission-block .col{color:var(--white);text-align:center}
.mission-col{width:501px;background:var(--steel);padding:74px 34px 0}
.quals-col{width:501px;background:var(--navy);padding:33px 28px 0}
.mission-block h2{font-family:"Orbitron",sans-serif;font-weight:500;font-size:28px;margin-bottom:18px}
.mission-col p{font-size:13.5px;line-height:28.5px}
.quals-col p{font-size:13px;line-height:25.7px}

/* map */
.site-map{position:absolute;top:2455px;left:119px;width:962px;height:544px;border-radius:42px;background:radial-gradient(ellipse at 48% 52%,#c8a46a 0%,#a8844e 40%,#6d5a3c 75%,#4a3f2e 100%);overflow:hidden}
.marker{position:absolute;width:26px;height:26px;border-radius:50%;background:var(--marker);box-shadow:0 0 0 7px rgba(59,91,245,.28),0 0 18px rgba(59,91,245,.8);color:var(--white);font-size:20px;line-height:25px;text-align:center;font-family:"Arimo",sans-serif}
.map-card{position:absolute;left:374px;top:242px;width:201px;height:83px;background:var(--white);border-radius:10px;padding:17px 22px;font-size:10.5px;font-weight:700;line-height:21px;color:var(--black)}

/* gallery */
.gallery{position:absolute;top:3100px;left:0;width:1200px;height:727px;background:var(--navy)}
.gallery .section-title{position:absolute;top:88px;width:1200px;color:var(--white)}
.gallery-item{position:absolute;width:232px;height:215px;border-radius:14px}

/* contact */
.contact{position:absolute;top:3827px;left:0;width:1200px;height:539px;background:var(--white)}
.contact .section-title{position:absolute;top:80px;width:1200px}
.field{position:absolute;background:var(--white);border-radius:6px;box-shadow:0 3px 14px rgba(0,0,0,.13);font-size:13px;color:#666;padding:15px 18px}
.submit{position:absolute;left:531px;top:380px;width:136px;height:49px;border-radius:25px;background:var(--navy);color:var(--white);font-weight:700;font-size:15px;text-align:center;line-height:49px;box-shadow:0 3px 10px rgba(0,0,0,.25)}

/* footer */
.site-footer{position:absolute;top:4366px;left:0;width:1200px;height:504px;background:var(--black);color:var(--white)}
.footer-badge{position:absolute;left:528px;top:72px;width:144px;height:144px;border-radius:50%;background:var(--navy);border:3px solid var(--white);display:flex;align-items:center;justify-content:center}
.footer-badge span{font-family:"Michroma",sans-serif;font-size:14px;text-align:center;line-height:1.6}
.footer-nav{position:absolute;top:252px;width:1200px;text-align:center;font-family:"Michroma",sans-serif;font-size:13px}
.footer-nav span{margin:0 17px}
.contact-item{position:absolute;top:313px;display:flex;align-items:center;gap:25px;font-size:14.5px}
.contact-icon{width:48px;height:48px;background:var(--steel);display:flex;align-items:center;justify-content:center}
.copyright{position:absolute;top:416px;width:1200px;text-align:center;font-size:14.5px}
.copyright em{font-style:normal;color:var(--steel-light)}
</style>
</head>
<body>

<header class="site-header">
  <a style="left:97px">Mission</a>
  <a style="left:215px">What We Provide</a>
  <a style="left:424px">Map</a>
  <a style="left:745px">Qualifications</a>
  <a style="left:917px">Contact</a>
  <a style="left:1035px">Gallery</a>
  <div class="brand-badge"><span>VELMO<br>TRAIL</span></div>
</header>

<section class="hero">
  <div role="img" aria-label="Operator with headset and backpack watching a helicopter land on a green mountain slope with snow patches" style="position:absolute;inset:0"></div>
  <div class="hero-panel">
    <h1>VELMOTRAIL</h1>
    <p>Master The Mission</p>
  </div>
</section>

<section class="provide">
  <h2 class="section-title">What We Provide</h2>
  <p class="lead">At Velmo Trail, we draw upon years of invaluable experience gained from training at SOF facilities worldwide. Our journey has culminated in the creation of an all-encompassing training site tailored to meet the exacting needs of SOF operators. We provide a comprehensive range of training modalities meticulously crafted to enhance SOF tactics. Anchored by an unwavering commitment to realism and operational effectiveness, we ensure that your warriors are fully prepared to conquer the most demanding challenges they may face.</p>

  <div class="feature top">
    <h3>TACTICAL VEHICLES</h3>
    <p>Our designated area enables rigorous vehicular-based training, empowering operators<br>to navigate terrain with confidence and precision.</p>
  </div>

  <svg class="spine" width="1200" height="1191" viewBox="0 0 1200 1191" aria-hidden="true">
    <g stroke="#b9bec8" stroke-width="1.2" stroke-dasharray="5 4" fill="none">
      <line x1="585" y1="500" x2="585" y2="1010"/>
      <line x1="600" y1="500" x2="600" y2="1010"/>
      <line x1="615" y1="500" x2="615" y2="1010"/>
      <path d="M560 539 H585"/><path d="M640 539 H615"/>
      <path d="M560 730 H585"/><path d="M640 730 H615"/>
      <path d="M560 868 H585"/><path d="M640 868 H615"/>
    </g>
    <g fill="#fff" stroke="#121d3b" stroke-width="1.5">
      <circle cx="561" cy="539" r="5"/><circle cx="661" cy="539" r="5"/>
      <circle cx="561" cy="730" r="5"/><circle cx="661" cy="730" r="5"/>
      <circle cx="561" cy="868" r="5"/><circle cx="661" cy="868" r="5"/>
    </g>
    <circle cx="608" cy="1053" r="50" fill="#fff" stroke="#c9ced8" stroke-width="4"/>
    <circle cx="608" cy="1053" r="40" fill="#121d3b"/>
  </svg>

  <!-- hexagon icons -->
  <svg class="hex" style="left:566px;top:414px" viewBox="0 0 84 84" aria-hidden="true"><polygon points="42,3 78,22 78,62 42,81 6,62 6,22" fill="#4f81b6" stroke="#d3dbe8" stroke-width="3"/><path d="M28 54 V44 M36 54 V38 M44 54 V32 M52 54 V40" stroke="#fff" stroke-width="5"/><path d="M26 36 L40 28 L48 32 L58 24" stroke="#fff" stroke-width="2.5" fill="none"/></svg>
  <svg class="hex" style="left:478px;top:497px" viewBox="0 0 84 84" aria-hidden="true"><polygon points="42,3 78,22 78,62 42,81 6,62 6,22" fill="#121d3b" stroke="#d3dbe8" stroke-width="3"/><circle cx="42" cy="42" r="14" fill="none" stroke="#fff" stroke-width="3"/><circle cx="42" cy="42" r="4" fill="#fff"/><path d="M42 22 V30 M42 54 V62 M22 42 H30 M54 42 H62" stroke="#fff" stroke-width="2.5"/></svg>
  <svg class="hex" style="left:661px;top:497px" viewBox="0 0 84 84" aria-hidden="true"><polygon points="42,3 78,22 78,62 42,81 6,62 6,22" fill="#4f81b6" stroke="#d3dbe8" stroke-width="3"/><circle cx="42" cy="42" r="15" fill="none" stroke="#fff" stroke-width="3"/><path d="M35 42 L40 47 L50 36" stroke="#fff" stroke-width="3" fill="none"/></svg>
  <svg class="hex" style="left:478px;top:688px" viewBox="0 0 84 84" aria-hidden="true"><polygon points="42,3 78,22 78,62 42,81 6,62 6,22" fill="#4f81b6" stroke="#d3dbe8" stroke-width="3"/><path d="M24 52 H60 M30 52 L38 34 H50 L56 52" stroke="#fff" stroke-width="3" fill="none"/><path d="M42 26 V34" stroke="#fff" stroke-width="3"/></svg>
  <svg class="hex" style="left:661px;top:688px" viewBox="0 0 84 84" aria-hidden="true"><polygon points="42,3 78,22 78,62 42,81 6,62 6,22" fill="#121d3b" stroke="#d3dbe8" stroke-width="3"/><circle cx="44" cy="40" r="12" fill="none" stroke="#fff" stroke-width="3"/><path d="M35 49 L26 58" stroke="#fff" stroke-width="4"/></svg>
  <svg class="hex" style="left:478px;top:826px" viewBox="0 0 84 84" aria-hidden="true"><polygon points="42,3 78,22 78,62 42,81 6,62 6,22" fill="#121d3b" stroke="#d3dbe8" stroke-width="3"/><path d="M42 24 L60 38 H24 Z" fill="#fff"/><rect x="28" y="40" width="28" height="18" fill="none" stroke="#fff" stroke-width="3"/></svg>
  <svg class="hex" style="left:661px;top:826px" viewBox="0 0 84 84" aria-hidden="true"><polygon points="42,3 78,22 78,62 42,81 6,62 6,22" fill="#4f81b6" stroke="#d3dbe8" stroke-width="3"/><path d="M28 56 V46 M36 56 V40 M44 56 V34 M52 56 V28" stroke="#fff" stroke-width="5"/></svg>

  <div class="feature left" style="left:22px;top:464px">
    <h3>PRECISION MARKSMANSHIP</h3>
    <p>Utilizing Tier 1 level instructors alongside seasoned local tactical shooting experts, our comprehensive programs incorporate practice with both steel and paper targets, conducted across multiple shooting locations for varied training environments.</p>
  </div>
  <div class="feature" style="left:771px;top:464px">
    <h3>IMMERSIVE SCENARIOS</h3>
    <p>We have transformed a former Soviet military stronghold into a dynamic training environment, meticulously furnished with explosives, pyrotechnics, and a live Opposition Force for verisimilar assault scenarios.</p>
  </div>
  <div class="feature left" style="left:22px;top:655px">
    <h3>AIRFIELD DOMINANCE</h3>
    <p>With a sprawling 7000ft runway available, we provide an expansive canvas for a myriad of airfield operations, including seizures, static line operations, military free fall, and helicopter insertion and extraction techniques.</p>
  </div>
  <div class="feature" style="left:771px;top:655px">
    <h3>JTAC SUPPORT</h3>
    <p>Our team comprises skilled JTACs ready to replicate aircraft in Close Air Support simulations, guaranteeing operators engage in authentic training for air-to-ground coordination, sharpening the skills needed to execute precision strikes</p>
  </div>
  <div class="feature left" style="left:22px;top:846px">
    <h3>COMFORTABLE LODGING AND FACILITIES</h3>
    <p>We offer on-site accommodation and mission planning rooms, complete with meticulously prepared meals, as well as sauna and other recreational and fitness amenities. Additionally, transportation services can be readily arranged, ensuring operators are well-rested and fully prepared to engage in rigorous training exercises.</p>
  </div>
  <div class="feature" style="left:771px;top:846px">
    <h3>CULTURAL IMMERSION</h3>
    <p>Consider enriching your experience in this captivating region. Allow us to organize a cultural day, including a traditional Estonian sauna and grill experience, a guided tour of historical sites in Tallinn, and an evening filled with vibrant urban nightlife.</p>
  </div>
</section>

<p class="closing">At Velmo Trail OÜ, our paramount mission is to extend our hospitality to your esteemed team, immersing you in dynamic and authentic training scenarios that cover every aspect of your SOF prowess. We take charge of the logistical challenges, allowing your team to fully concentrate on mastering the mission in Eastern Europe. Our steadfast dedication ensures that every SOF warrior attains the pinnacle of performance and resolute readiness, empowering you to excel in your noble mission: the relentless pursuit of absolute victory with decisive force!</p>

<section class="mission-block">
  <div class="col mission-col">
    <h2>Mission</h2>
    <p>Pioneering realistic training within a strategic theater across the full spectrum of SOF capabilities, liberating warriors from the shackles of logistical burdens and unleashing their full potential to vanquish adversaries</p>
  </div>
  <div class="col quals-col">
    <h2>Qualifications Summary</h2>
    <p>The founders of Velmo Trail OÜ bring forth a wealth of experience and expertise to the table. A former USAF Combat Controller, with nearly a decade of service in Europe; and a highly esteemed former Estonian Special Operator who graduated BUDs and Ranger School, with a proven track record of business success in Estonia. Together, we are steadfast in our dedication to delivering world-class training experiences, deeply rooted in operational excellence and strategic foresight.</p>
  </div>
</section>

<section class="site-map" role="img" aria-label="Illustrated sand-toned site map of the training area showing ranges, buildings, roads and a runway">
  <div class="marker" style="left:369px;top:184px">+</div>
  <div class="marker" style="left:607px;top:117px">+</div>
  <div class="marker" style="left:318px;top:335px">+</div>
  <div class="marker" style="left:686px;top:320px">+</div>
  <div class="map-card">SITE-3<br>MULTIPLE SHOOTING LANES<br>TACTICAL VEHICLE AREA</div>
</section>

<section class="gallery">
  <h2 class="section-title">Our Gallery</h2>
  <div class="gallery-item" role="img" aria-label="Parachutist descending over open plains under a cloudy sky" style="left:98px;top:170px;background:linear-gradient(180deg,#9fb5cf,#c9d2d8 70%,#8f8a70)"></div>
  <div class="gallery-item" role="img" aria-label="Two operators in helmets reviewing a tablet on grass, seen from above" style="left:355px;top:170px;background:linear-gradient(160deg,#5f6b47,#3e4a32 60%,#6b7a4c)"></div>
  <div class="gallery-item" role="img" aria-label="Helicopter landing on a green mountain slope" style="left:614px;top:170px;background:linear-gradient(180deg,#6a7660,#5a7a3c 60%,#3f5a2a)"></div>
  <div class="gallery-item" role="img" aria-label="Operators in a field at dusk with radio antennas" style="left:871px;top:170px;background:linear-gradient(180deg,#6e747a,#8c7a5a 60%,#5a4a32)"></div>
  <div class="gallery-item" role="img" aria-label="Night training with vehicles on an airfield apron" style="left:98px;top:415px;background:linear-gradient(180deg,#1c1a18,#4a3c24 60%,#8a7040)"></div>
  <div class="gallery-item" role="img" aria-label="Free-fall parachutist high above snowy terrain" style="left:355px;top:415px;background:linear-gradient(180deg,#8aa0b8,#b9c7d3 60%,#7f93a8)"></div>
  <div class="gallery-item" role="img" aria-label="Operator on a shooting range on a grey overcast day" style="left:614px;top:415px;background:linear-gradient(180deg,#c4cbd0,#7a8a6a 50%,#4a4f4a)"></div>
  <div class="gallery-item" role="img" aria-label="Vehicles and operators on an airfield at night" style="left:871px;top:415px;background:linear-gradient(180deg,#1a1816,#4e3e26 60%,#8e7342)"></div>
</section>

<section class="contact">
  <h2 class="section-title">Contact Us</h2>
  <div class="field" style="left:181px;top:148px;width:411px;height:47px">Name</div>
  <div class="field" style="left:607px;top:148px;width:410px;height:47px">Email</div>
  <div class="field" style="left:181px;top:210px;width:411px;height:47px">Phone Number</div>
  <div class="field" style="left:607px;top:210px;width:410px;height:47px">Subject</div>
  <div class="field" style="left:181px;top:272px;width:836px;height:84px">Message</div>
  <div class="submit">Submit</div>
</section>

<footer class="site-footer">
  <div class="footer-badge"><span>VELMO<br>TRAIL</span></div>
  <nav class="footer-nav"><span>Mission</span><span>What We Provide</span><span>Map</span><span>Qualifications</span><span>Contact</span><span>Gallery</span></nav>
  <div class="contact-item" style="left:146px">
    <div class="contact-icon"><svg width="24" height="18" viewBox="0 0 24 18" aria-hidden="true"><rect x="1" y="1" width="22" height="16" fill="#fff"/><path d="M1 1 L12 10 L23 1" stroke="#4f81b6" stroke-width="2" fill="none"/></svg></div>
    <span>info@velmotrail.com</span>
  </div>
  <div class="contact-item" style="left:514px">
    <div class="contact-icon"><svg width="18" height="24" viewBox="0 0 18 24" aria-hidden="true"><path d="M9 1 C4 1 1 4.5 1 9 C1 15 9 23 9 23 C9 23 17 15 17 9 C17 4.5 14 1 9 1 Z" fill="#fff"/><circle cx="9" cy="9" r="3" fill="#4f81b6"/></svg></div>
    <span>Velmotrail, United States.</span>
  </div>
  <div class="contact-item" style="left:855px">
    <div class="contact-icon"><svg width="22" height="22" viewBox="0 0 24 24" aria-hidden="true"><path d="M6.6 10.8c1.4 2.8 3.8 5.1 6.6 6.6l2.2-2.2c.3-.3.7-.4 1-.2 1.1.4 2.3.6 3.6.6.6 0 1 .4 1 1V20c0 .6-.4 1-1 1C10.6 21 3 13.4 3 4c0-.6.4-1 1-1h3.5c.6 0 1 .4 1 1 0 1.3.2 2.5.6 3.6.1.3 0 .7-.2 1L6.6 10.8z" fill="#fff"/></svg></div>
    <span>+1 555 014 2377</span>
  </div>
  <p class="copyright">Copyrights@2024.<em>Company Name</em>.All Rights Reserved</p>
</footer>

</body>
</html>
```